full stationary design for a modern sleek design company

we are a design company that does modern minimalistic interior design works as well as other design services for high end clients.
we need a full stationary design including and not limited to (double sided business card, letter head, envelopes, documents folder...etc) that reflects the modern style design we do.
sleek modern and minimalistic is the requirements.
Updates

please use the latest attached files as there was a slight modification on the logo Added Wednesday, March 1, 2017

minor update on the logo files in JPG and PSD has been updated kindly follow the new attachments. Added Thursday, March 2, 2017

Target Market(s)

modern minimalist clients

Industry/Entity Type

Design Agency

Requirements
Must have
• the logo
Nice to have
• i like the colors in the colored 3D logo attached
Should not have
• too many colors

```html
<!DOCTYPE html>
<html lang="en">
<head>
<meta charset="utf-8">
<title>Linea Atelier – Business Card</title>
<link href="https://fonts.googleapis.com/css2?family=Open+Sans:wght@400;600;700&display=swap" rel="stylesheet">
<style>
  :root {
    --backdrop: #d9d6d1;
    --card: #f4f3f1;
    --ink: #2b2b2b;
    --ink-soft: #3a3a3a;
    --accent: #e0661e;
    --accent-deep: #c9561a;
    --bar-dark: #2a2a2a;
    --band-text: #fbe6d8;
  }
  * { margin: 0; padding: 0; box-sizing: border-box; }
  html, body {
    width: 1200px; height: 969px; overflow: hidden;
    background: var(--backdrop);
    font-family: "Open Sans", Arial, sans-serif;
    color: var(--ink);
  }
  .business-card {
    position: absolute; left: 120px; top: 211px;
    width: 960px; height: 548px;
    background: var(--card);
    border-radius: 8px 66px 8px 8px;
    overflow: hidden;
    box-shadow: 0 6px 24px rgba(0,0,0,0.12);
  }
  .brand {
    position: absolute; left: 58px; top: 82px;
    display: flex; align-items: center; gap: 18px;
  }
  .brand-square { width: 54px; height: 54px; background: var(--accent); }
  .brand-name {
    font-weight: 700; font-size: 52px; letter-spacing: 2px;
    color: var(--ink); line-height: 1; text-transform: uppercase;
  }
  .person { position: absolute; right: 52px; top: 168px; text-align: right; }
  .person-name {
    font-weight: 600; font-size: 30px; color: var(--accent);
    letter-spacing: 0.5px; line-height: 1.2;
  }
  .person-title { font-size: 24px; color: var(--ink-soft); line-height: 1.3; }
  .divider {
    position: absolute; left: 270px; top: 387px;
    width: 638px; height: 2px; background: var(--ink);
  }
  .contact-list {
    position: absolute; left: 52px; top: 368px; list-style: none;
  }
  .contact-list li {
    display: flex; align-items: center; gap: 14px;
    font-size: 24px; line-height: 37px; color: var(--ink-soft);
  }
  .contact-list svg { width: 22px; height: 22px; fill: var(--accent); flex: none; }
  .address {
    position: absolute; right: 52px; top: 404px; text-align: right;
    font-size: 24px; line-height: 36px; color: var(--ink-soft);
  }
  .footer-bar {
    position: absolute; left: 28px; top: 537px;
    width: 498px; height: 11px; background: var(--bar-dark);
  }
  .web-band {
    position: absolute; left: 535px; top: 496px;
    width: 425px; height: 52px;
    background: linear-gradient(90deg, var(--accent), var(--accent-deep));
    border-top-left-radius: 16px;
    display: flex; align-items: center; justify-content: center;
    font-size: 23px; letter-spacing: 2px; color: var(--band-text);
  }
</style>
</head>
<body>
  <div class="business-card">
    <div class="brand">
      <span class="brand-square"></span>
      <span class="brand-name">Linea Atelier</span>
    </div>

    <div class="person">
      <div class="person-name">ADAM REYES</div>
      <div class="person-title">CEO&amp;Founder</div>
    </div>

    <div class="divider"></div>

    <ul class="contact-list">
      <li>
        <svg viewBox="0 0 24 24" aria-hidden="true"><path d="M6.6 10.8a15.1 15.1 0 0 0 6.6 6.6l2.2-2.2c.3-.3.7-.4 1-.2 1.1.4 2.3.6 3.6.6.6 0 1 .4 1 1V20c0 .6-.4 1-1 1A17 17 0 0 1 3 4c0-.6.4-1 1-1h3.5c.6 0 1 .4 1 1 0 1.3.2 2.5.6 3.6.1.3 0 .7-.2 1z"/></svg>
        (555) 210 4817
      </li>
      <li>
        <svg viewBox="0 0 24 24" aria-hidden="true"><path d="M7 1h10a2 2 0 0 1 2 2v18a2 2 0 0 1-2 2H7a2 2 0 0 1-2-2V3a2 2 0 0 1 2-2zm0 3v14h10V4zm5 15.2a1.1 1.1 0 1 0 0 2.2 1.1 1.1 0 0 0 0-2.2z"/></svg>
        (555) 382 6094
      </li>
      <li>
        <svg viewBox="0 0 24 24" aria-hidden="true"><path d="M2 5h20v14H2zm2 2v.4l8 5 8-5V7zm0 2.8V17h16V9.8l-8 5z"/></svg>
        adam@lineaatelier.com
      </li>
    </ul>

    <div class="address">
      2140 Harbor Lane<br>
      Fairview, Oregon 97024
    </div>

    <div class="footer-bar"></div>
    <div class="web-band">www.lineaatelier.com</div>
  </div>
</body>
</html>
```